Business Card - high end, modern health care

Hey designers!

We need a double sided business card for the boutique, cutting edge physical therapy rehabilitation centre in Sydney's Northern Beaches.

With the most qualified physios in the area The Harbourview Motion Clinic does what other physiotherapy practices do not, we take our time with our patients giving them longer appointments, better physios and therefor faster results!

We guarantee that the service people receive at THMC will be unparalleled.

Hence we need a business card to reflect our modern, boutique, high end service. The final design needs to reflect that we are in a class of our own yet with the feel of beachside retreat.

Below I have attached our logo in both blue on white and white on blue. The exact colour is;
and the font that we have used in our logo is Tex Gyre Aventador.

I like the idea of the blue as the main colour as it is more eye catching and our signage onto the main road will be in this blue and in the interest of consistency across marketing the blue needs to be a part of the design. However I would appreciate a few designs onto a wooden background as this is a visual theme within the fitout of the practice.

The design needs to be of standard size (91x55mm).

Target Market(s)

We target people who have an end outcome in mind and those who have had poor experiences with other providers and ensure that everyone gets the care that they deserve with a premium service that is tailored to the individuals circumstances. As a premium service, the target market is highly educated, business and tech savvy with the additional target market of elderly people who have self funded their retirement and see value in paying for the best ongoing rehabilitation to maintain independence.

Industry/Entity Type

Physical Therapy

Contact Information for Business Card

Name, designation( Titled Musculoskeletal Physiotherapist... there will also be those in the company that have multiple designations ie 5 or 6 words long), phone number, email, facebook, instagram, address

Font styles to use
Sans Serif

Colors

Designer to choose colors to be used in the design.

Requirements
Must have
• Front - The logo as large as possible, blue or wooden theme, and all of the important details.
• Back - A blank space/lines on which to write appointment times (no "Appointment, date, time" etc.)
Nice to have
• facebook url
• logos for facebook and instagram
• Mini logos for the phone and email?

```html
<!DOCTYPE html>
<html lang="en">
<head>
<meta charset="UTF-8">
<title>The Harbourview Motion Clinic – Business Card</title>
<link rel="stylesheet" href="https://fonts.googleapis.com/css2?family=Montserrat:wght@600;700&display=swap">
<style>
  :root {
    --brand-blue: #0c56a6;
    --card-white: #ffffff;
    --card-back: #f1f2f4;
    --stage: #222324;
    --text-on-blue: #ffffff;
  }
  * { margin: 0; padding: 0; box-sizing: border-box; }
  html, body {
    width: 1200px; height: 960px; overflow: hidden;
    background: var(--stage);
    font-family: "Montserrat", Arial, sans-serif;
  }
  .canvas { position: relative; width: 1200px; height: 960px; }
  .card {
    position: absolute; width: 600px; height: 342px;
    border-radius: 18px; overflow: hidden;
  }
  .card--front { left: 322px; top: 108px; background: var(--card-white); }
  .card--back { left: 320px; top: 493px; background: var(--card-back); }

  .details-panel {
    position: absolute; left: 0; top: 0; width: 283px; height: 100%;
    background: var(--brand-blue); color: var(--text-on-blue);
  }
  .person-name {
    position: absolute; left: 40px; top: 73px;
    font-size: 23px; font-weight: 700; letter-spacing: 0.3px;
  }
  .person-title {
    position: absolute; left: 40px; top: 101px;
    font-size: 14.5px; font-weight: 700;
  }
  .address {
    position: absolute; left: 40px; top: 131px;
    font-size: 14.5px; font-weight: 600; line-height: 19px;
  }
  .contact-list {
    position: absolute; left: 40px; top: 180px; list-style: none;
  }
  .contact-item {
    display: flex; align-items: center; height: 19px;
    font-size: 14.5px; font-weight: 600;
  }
  .contact-icon {
    width: 14px; height: 14px; margin-right: 10px; flex: none;
  }

  .brand-block {
    position: absolute; left: 283px; top: 0; width: 317px; height: 100%;
    color: var(--brand-blue); text-align: center;
  }
  .brand-name {
    position: absolute; left: 0; right: 0; top: 104px;
    font-weight: 700; line-height: 1;
  }
  .brand-name__line1 { display: block; font-size: 24px; letter-spacing: 0.5px; }
  .brand-name__line2 { display: block; font-size: 15.5px; letter-spacing: 4px; margin-top: 6px; }
  .brand-dot {
    position: absolute; left: 108px; top: 170px;
    width: 100px; height: 100px; border-radius: 50%;
    background: var(--brand-blue);
  }
</style>
</head>
<body>
<main class="canvas">
  <section class="card card--front" aria-label="Card front">
    <div class="details-panel">
      <h1 class="person-name">LIAM CARTER</h1>
      <p class="person-title">CEO/FOUNDER</p>
      <p class="address">42 Pittwater Road<br>Dee Why, NSW 2099</p>
      <ul class="contact-list">
        <li class="contact-item">
          <svg class="contact-icon" viewBox="0 0 24 24" fill="#fff"><path d="M6.6 10.8a15.1 15.1 0 0 0 6.6 6.6l2.2-2.2a1 1 0 0 1 1-.25 11.4 11.4 0 0 0 3.6.57 1 1 0 0 1 1 1V20a1 1 0 0 1-1 1A17 17 0 0 1 3 4a1 1 0 0 1 1-1h3.5a1 1 0 0 1 1 1c0 1.25.2 2.45.57 3.57a1 1 0 0 1-.25 1z"/></svg>
          02 8765 4321
        </li>
        <li class="contact-item">
          <svg class="contact-icon" viewBox="0 0 24 24" fill="#fff"><path d="M2 5h20v14H2z" /><path d="M2 5l10 8 10-8" fill="none" stroke="#0c56a6" stroke-width="2"/></svg>
          liam@hvmotion.com
        </li>
        <li class="contact-item">
          <svg class="contact-icon" viewBox="0 0 24 24" fill="none" stroke="#fff" stroke-width="2"><circle cx="12" cy="12" r="10"/><path d="M2 12h20M12 2c3 3 3 17 0 20M12 2c-3 3-3 17 0 20"/></svg>
          www.hvmotion.com
        </li>
        <li class="contact-item">
          <svg class="contact-icon" viewBox="0 0 24 24"><rect x="2" y="2" width="20" height="20" rx="2" fill="#fff"/></svg>
          /hvmotionclinic
        </li>
        <li class="contact-item">
          <svg class="contact-icon" viewBox="0 0 24 24"><rect x="2" y="2" width="20" height="20" rx="2" fill="#fff"/></svg>
          @hvmotion
        </li>
      </ul>
    </div>
    <div class="brand-block">
      <p class="brand-name">
        <span class="brand-name__line1">THE HARBOURVIEW</span>
        <span class="brand-name__line2">MOTION CLINIC</span>
      </p>
      <div class="brand-dot" aria-hidden="true"></div>
    </div>
  </section>

  <section class="card card--back" aria-label="Card back, blank for appointment notes"></section>
</main>
</body>
</html>
```